Need Help having my business card stand out

I am the owner of Birchway Canine Training and would like for my business cards to stand out. I have been trying to keep designing them myself but I can't get what I have in my head on the card. I will try my best to post templates that I like for inspirations. I want something unique but elegant. I don't want in to look cartoony or cheesy. It needs to pop in a pet shop but also in a coffee shop or gym.

Target Market(s)

Dog owners, Married ,No young kids Jr High school kids and up (maybe kids on the way) Executives, Stay at home moms/wives, Small business owners

Industry/Entity Type

Dog Training

Contact Information for Business Card

Lowell Spratt, 281-904-3376, info@birchwaycanine.example, www.birchwaycanine.example

Colors

Designer to choose colors to be used in the design.

Requirements
Must have
• my logo
Should not have
• Cursive lettering

```html
<!DOCTYPE html>
<html lang="en">
<head>
<meta charset="utf-8">
<title>Birchway Canine Training – Business Card</title>
<link rel="stylesheet" href="https://fonts.googleapis.com/css2?family=Nunito+Sans:wght@400;600;700;800&display=swap">
<style>
  :root {
    --backdrop: #7a7a7a;
    --card-light: #ffffff;
    --card-dark: #2e2e2e;
    --ink: #1f1f1f;
    --ink-soft: #6d6d6d;
    --ink-body: #444444;
    --ink-reverse: #ffffff;
    --rule-reverse: #e6e6e6;
    --art-top: #4a4a4a;
    --art-bottom: #3a3a3a;
  }
  * { box-sizing: border-box; margin: 0; padding: 0; }
  html, body {
    width: 1200px; height: 914px; overflow: hidden;
    background: var(--backdrop);
    font-family: "Nunito Sans", Arial, sans-serif;
  }
  .stage {
    position: relative; width: 1200px; height: 914px;
    display: flex; justify-content: center; align-items: center; gap: 70px;
  }
  .card {
    position: relative; width: 330px; height: 578px;
    box-shadow: 0 18px 40px rgba(0,0,0,.28);
  }
  .card--front { background: var(--card-light); color: var(--ink); }
  .card--back { background: var(--card-dark); color: var(--ink-reverse); }

  /* front */
  .front-brand {
    position: absolute; top: 56px; left: 0; right: 0;
    display: flex; align-items: center; justify-content: center; gap: 8px;
  }
  .front-brand__dot { width: 12px; height: 12px; background: var(--ink); border-radius: 50%; }
  .front-brand__name { font-size: 17px; font-weight: 800; letter-spacing: .02em; }
  .person { position: absolute; top: 150px; left: 34px; }
  .person__name { font-size: 22px; font-weight: 700; }
  .person__role { font-size: 13px; color: var(--ink-soft); margin-top: 2px; }
  .contacts { position: absolute; top: 250px; left: 34px; right: 30px; list-style: none; }
  .contacts li {
    display: flex; align-items: flex-start; gap: 10px;
    font-size: 12.5px; line-height: 1.45; color: var(--ink-body); margin-bottom: 10px;
  }
  .contacts svg { flex: 0 0 16px; margin-top: 1px; }

  /* back */
  .tagline {
    position: absolute; top: 130px; left: 0; right: 0; text-align: center;
    font-size: 11px; font-weight: 700; letter-spacing: .18em;
  }
  .mark-art {
    position: absolute; top: 160px; left: 120px; width: 90px; height: 100px;
    background: linear-gradient(var(--art-top), var(--art-bottom)); border-radius: 6px;
  }
  .back-brand {
    position: absolute; top: 270px; left: 0; right: 0; text-align: center;
    font-size: 20px; font-weight: 800; line-height: 1.25; padding: 0 30px;
  }
  .back-rule {
    position: absolute; top: 332px; left: 0; right: 0; height: 2px;
    background: var(--rule-reverse);
  }
  .back-url {
    position: absolute; bottom: 72px; left: 0; right: 0; text-align: center;
    font-size: 14px; font-weight: 700; letter-spacing: .02em;
  }
</style>
</head>
<body>
<main class="stage">
  <section class="card card--front" aria-label="Business card front">
    <div class="front-brand">
      <span class="front-brand__dot"></span>
      <span class="front-brand__name">Birchway Canine Training</span>
    </div>
    <div class="person">
      <p class="person__name">Lowell Spratt</p>
      <p class="person__role">Designation</p>
    </div>
    <ul class="contacts">
      <li>
        <svg width="16" height="16" viewBox="0 0 16 16"><circle cx="8" cy="8" r="7.5" fill="#333"/><path d="M8 3.5a2.6 2.6 0 0 0-2.6 2.6C5.4 8 8 11.5 8 11.5s2.6-3.5 2.6-5.4A2.6 2.6 0 0 0 8 3.5z" fill="#fff"/></svg>
        <span>#48 Fernhill Road, Eastvale Park, Texas, 77000, USA</span>
      </li>
      <li>
        <svg width="16" height="16" viewBox="0 0 16 16"><circle cx="8" cy="8" r="7.5" fill="#333"/><rect x="5.5" y="3.5" width="5" height="9" rx="1" fill="#fff"/></svg>
        <span>281-904-3376</span>
      </li>
      <li>
        <svg width="16" height="16" viewBox="0 0 16 16"><circle cx="8" cy="8" r="7.5" fill="#333"/><rect x="4" y="5" width="8" height="6" fill="#fff"/><path d="M4 5l4 3.2L12 5" stroke="#333" fill="none"/></svg>
        <span>info@birchwaycanine.example</span>
      </li>
      <li>
        <svg width="16" height="16" viewBox="0 0 16 16"><circle cx="8" cy="8" r="7.5" fill="#333"/><circle cx="8" cy="8" r="4" fill="none" stroke="#fff"/><path d="M4 8h8M8 4c-2 2.5-2 5.5 0 8M8 4c2 2.5 2 5.5 0 8" stroke="#fff" fill="none" stroke-width=".8"/></svg>
        <span>www.birchwaycanine.example</span>
      </li>
    </ul>
  </section>

  <section class="card card--back" aria-label="Business card back">
    <p class="tagline">CALM DOGS, HAPPY HOMES</p>
    <div class="mark-art" role="img" aria-label="Area for the brand illustration of a dog"></div>
    <p class="back-brand">Birchway Canine Training</p>
    <div class="back-rule"></div>
    <p class="back-url">www.birchwaycanine.example</p>
  </section>
</main>
</body>
</html>
```